Need Website Design for Non-Profit Veteran Site

I am looking for a very talented creative website designer for a modern feel. I'll give a little bit of guidance around what I am looking for and then your creative juices should kick in and design away. I have already purchased the domain but will need hosting (at least temporarily) and the creative design work done.The website domain is militarydocs.orgI am looking to attract current and veteran military providers (doctors, nurse practitioners, physician assistants, etc) to join and signup for membership. They would pay a yearly fee to join. Would need membership categories $135 for Provider, $55 Student, $100 for Retired, and Organization (Organization would be broken down into Less than 100 ($200), 100-249 ($250), 250-499 ($300), 500-999 ($400), 1,000-2,999 ($500), and 3,000 ($700). Would need Benefit built out and would need to accept money through CoinVane and other means. Since it's a new organization just starting, would also need a Donate button to get people to donate if they want any amount they would like. The second part of the website is that once they join, they will have acess to a list of all other providers who have registered within the website (not exportable) so they can connect with one another. If they want to see contact information this will be included in their fee as a benefit to socialize with one another. As part of the website, there will be another Veteran's portal so veterans who would like to connect with a provider around a particular speciality can reach out and request help from the doctor writing a nexus letter or letter to support the veteran who is filing a claim with the BQ. Veterans would pay a yearly sign-up fee of $30.00 and would need their membership benefits displayed. They would have access to a list of veterans in their region by state and distance, and can reach out to doctors to get their help. If a doctor and veteran agree, sharable inforamtion of medical hipaa documents can be exchanged via the website. The physician and veteran can negotiate a fee through the website only and share their details. This is a separate fee for this type of process between the provider and veteran. We will collect a $250 fee for admin on each of these and each project the veteran does with the provider will cost $450 (so essentially the doctor gets paid $450 and i get $250.00. This model could be changed over time as we start to test this out). A good example of 50% of what I'm looking for is something like the following website: https://www.lpkt.org/ It has some of the features but not all and my site should be more modernized to attract the veteran and military providers.

Target Market(s)

Current and retired military providers and veterans

Industry/Entity Type

Non Profit

Number of Pages Required

1 page

Requirements
Must have
• Military Design
• Modern Feel (Example templates for feel -https://quillmoth.com/free-photoshop-psd-web-design-template/)
• Donation box
• Stuff mentioned in the description)
Nice to have
• Open to feedback
Should not have
• Open to feedback

```html
<!DOCTYPE html>
<html lang="en">
<head>
<meta charset="utf-8">
<title>Harborwell Net</title>
<link href="https://fonts.googleapis.com/css2?family=Raleway:wght@500;600;700;800&family=Open+Sans:wght@400;600;700&display=swap" rel="stylesheet">
<style>
:root{
  --page:#8b9383;
  --camo:#2a3023;
  --nav:#2f3a22;
  --panel:#4a5040;
  --card:#6f7464;
  --accent:#9db55b;
  --accent-text:#c4d39a;
  --white:#ffffff;
  --soft:#e4e6df;
}
*{box-sizing:border-box;margin:0;padding:0}
html,body{width:1200px;height:2302px;overflow:hidden}
body{background:var(--page);font-family:"Open Sans",sans-serif;color:var(--white);position:relative}
.abs{position:absolute}
.camo{background:linear-gradient(135deg,#2b3124 0%,#3a4130 30%,#262b20 55%,#353b2b 80%,#2a3023 100%)}
.site-header{left:0;top:0;width:1200px;height:126px}
.brand{left:98px;top:34px;font-family:"Raleway",sans-serif;font-weight:800;font-size:23px;letter-spacing:.3px}
.search{left:565px;top:28px;width:241px;height:34px;border-bottom:1px solid #9aa08f;font-size:14px;color:#d5d8cd;padding-top:2px}
.search svg{position:absolute;right:2px;top:2px}
.pill{border:2px solid var(--white);border-radius:22px;font-weight:700;font-size:14px;display:flex;align-items:center;justify-content:center;gap:7px;font-family:"Open Sans",sans-serif}
.btn-join{left:845px;top:26px;width:122px;height:41px}
.btn-sign{left:979px;top:26px;width:121px;height:41px}
.main-nav{left:98px;top:100px;width:1002px;height:47px;background:var(--nav);display:flex;align-items:center;justify-content:space-between;padding:0 24px 0 25px;font-size:15px;font-weight:600}
.main-nav .on{color:var(--accent)}
.hero{left:98px;top:147px;width:1002px;height:415px;background:linear-gradient(90deg,#6d6a4e 0%,#857a5c 35%,#8a7558 60%,#6b5a45 100%)}
.hero-title{left:655px;top:245px;font-family:"Raleway",sans-serif;font-size:44px;font-weight:500;letter-spacing:.5px}
.hero-title b{font-weight:800}
.hero-text{left:657px;top:312px;width:380px;font-size:18px;line-height:27px;color:var(--soft)}
.btn-fill{background:var(--accent);border-radius:24px;font-weight:700;display:flex;align-items:center;justify-content:center;color:var(--white)}
.hero-btn{left:657px;top:424px;width:164px;height:43px;font-size:16px}
.dots{left:565px;top:507px;display:flex;gap:7px}
.dots i{width:14px;height:14px;border-radius:50%;border:2px solid var(--white)}
.dots i:first-child{background:var(--white)}
.welcome{left:98px;top:562px;width:1002px;height:706px;background:var(--panel)}
.section-title{font-family:"Raleway",sans-serif;font-size:30px;font-weight:500;color:var(--accent-text)}
.section-title b{font-weight:800}
.welcome-title{left:0;top:616px;width:1200px;text-align:center}
.welcome-text{left:190px;top:678px;width:820px;text-align:center;font-size:15px;line-height:26px;color:var(--soft)}
.card{width:304px;height:373px;top:795px;background:var(--card);border:3px solid #878b7c}
.card-photo{position:absolute;left:0;top:0;width:298px;height:189px}
.card h3{position:absolute;top:218px;width:100%;text-align:center;font-family:"Raleway",sans-serif;font-size:21px;font-weight:700;letter-spacing:.4px}
.card p{position:absolute;top:258px;left:22px;right:22px;text-align:center;font-size:14.5px;line-height:23px;color:var(--soft)}
.card-btn{top:1145px;height:44px;font-size:14px}
.banner{left:98px;top:1268px;width:1002px;height:217px;background:linear-gradient(90deg,#7c6a53 0%,#a0876a 30%,#7a5b45 60%,#4a3428 80%,#8a6a40 100%)}
.banner-text{left:0;top:1316px;width:1200px;text-align:center;font-family:"Raleway",sans-serif;font-weight:700;font-size:34px}
.banner-text b{font-weight:800;font-size:40px}
.outline{border:2px solid var(--white);border-radius:24px;font-weight:700;font-size:15px;display:flex;align-items:center;justify-content:center}
.banner-btn{left:522px;top:1383px;width:156px;height:47px}
.lower{left:98px;top:1485px;width:1002px;height:550px;background:var(--panel)}
.benefits-title{left:118px;top:1548px}
.news-title{left:596px;top:1548px}
.benefits-text{left:120px;top:1606px;width:430px;font-size:14.5px;line-height:24px;color:var(--soft)}
.benefit-list{left:120px;top:1677px;list-style:none;font-size:14.5px;color:var(--soft)}
.benefit-list li{height:30px;display:flex;align-items:center;gap:12px}
.read-btn{left:120px;top:1913px;width:127px;height:40px}
.view-btn{left:600px;top:1913px;width:127px;height:40px}
.news-photo{left:600px;width:132px;height:112px;border:3px solid var(--white)}
.news-item h4{position:absolute;left:755px;font-family:"Raleway",sans-serif;font-size:20px;font-weight:600}
.news-meta{position:absolute;left:757px;font-size:12.5px;color:var(--soft);display:flex;align-items:center;gap:6px}
.news-item p{position:absolute;left:757px;width:330px;font-size:13.5px;line-height:24px;color:var(--soft)}
.site-footer{left:0;top:2035px;width:1200px;height:267px}
.ficon{width:46px;height:46px;border:2px solid #d9dcd3;border-radius:50%;display:flex;align-items:center;justify-content:center}
.ftext{font-size:14px;line-height:22px;color:var(--soft)}
.foot-nav{left:0;top:2164px;width:1200px;text-align:center;font-size:14.5px;color:var(--soft);word-spacing:2px}
.foot-nav span{margin:0 14px;color:#bfc3b6}
.rule{left:98px;top:2216px;width:1002px;height:1px;background:#4b5142}
.copyright{left:100px;top:2242px;font-size:12.5px;color:var(--soft)}
.social{top:2233px;width:36px;height:36px;border:2px solid #d9dcd3;border-radius:50%}
</style>
</head>
<body>
<header class="abs site-header camo">
  <div class="abs brand">HARBORWELL NET</div>
  <div class="abs search">Search
    <svg width="16" height="16" viewBox="0 0 16 16"><circle cx="6.5" cy="6.5" r="5" fill="none" stroke="#fff" stroke-width="2"/><line x1="10.5" y1="10.5" x2="15" y2="15" stroke="#fff" stroke-width="2.4"/></svg>
  </div>
  <div class="abs pill btn-join">
    <svg width="16" height="14" viewBox="0 0 16 14"><circle cx="8" cy="4" r="3" fill="#fff"/><path d="M2 14c0-4 3-6 6-6s6 2 6 6z" fill="#fff"/></svg>JOIN US!</div>
  <div class="abs pill btn-sign">
    <svg width="13" height="13" viewBox="0 0 13 13"><path d="M1 12l1-4 7-7 3 3-7 7z" fill="#fff"/></svg>SIGNUP</div>
</header>

<nav class="abs main-nav">
  <span class="on">HOME</span><span>ABOUT US</span><span>SERVICES</span><span>PROGRAMS</span><span>MEMBERSHIP</span><span>NEWS</span><span>CAREER</span><span>CONTACT US</span>
</nav>

<section class="abs hero" role="img" aria-label="Close-up of a soldier's camouflage sleeve with a flag patch"></section>
<h1 class="abs hero-title"><b>HARBORWELL</b> NET</h1>
<p class="abs hero-text">Veteran military providers (doctors, nurse practitioners, physician assistants, etc) to join and signup for membership.</p>
<div class="abs btn-fill hero-btn">DONATE NOW</div>
<div class="abs dots"><i></i><i></i><i></i><i></i></div>

<section class="abs welcome"></section>
<h2 class="abs section-title welcome-title"><b>WELCOME TO</b> HARBORWELL NET</h2>
<p class="abs welcome-text">Nam libero tempore, cum soluta nobis est eligendi optio cumque nihil impedit quo minus id quod maxime placeat facere possimus, omnis voluptas assumenda est, omnis dolor repellendu oribus autem quibusdam et aut officiis debitis aut rerum necessitatibus saepe eveniet ut et voluptates repudiandae sint et molestiae.</p>

<article class="abs card" style="left:120px">
  <div class="card-photo" role="img" aria-label="Soldier in uniform standing before a striped flag" style="background:linear-gradient(90deg,#d96a80,#c9a7a0 45%,#6e6a55)"></div>
  <h3>VETERANS</h3>
  <p>Temporibus autem quibusdam et aut officiis debitis aut rerum necessitatibus saepe eveniet utv oluptate.</p>
</article>
<article class="abs card" style="left:448px">
  <div class="card-photo" role="img" aria-label="Doctor with a clipboard talking with a service member" style="background:linear-gradient(90deg,#9aa7b0,#dfe3e6 40%,#6d6f63)"></div>
  <h3>GET INVOLVED</h3>
  <p>Temporibus autem quibusdam et aut officiis debitis aut rerum necessitatibus saepe eveniet utv oluptate.</p>
</article>
<article class="abs card" style="left:776px">
  <div class="card-photo" role="img" aria-label="Two older veterans in caps saluting by the sea" style="background:linear-gradient(180deg,#7fa9d2,#4f7fa8 60%,#3b4a5e)"></div>
  <h3>MEMBERSHIP</h3>
  <p>Temporibus autem quibusdam et aut officiis debitis aut rerum necessitatibus saepe eveniet utv oluptate.</p>
</article>
<div class="abs btn-fill card-btn" style="left:184px;width:176px">NEED CLAIMS HELP?</div>
<div class="abs btn-fill card-btn" style="left:512px;width:176px">DONATE NOW!</div>
<div class="abs btn-fill card-btn" style="left:840px;width:176px">JOIN / SIGN UP</div>

<section class="abs banner" role="img" aria-label="Silhouette of a soldier holding a flag at sunset"></section>
<h2 class="abs banner-text">YEARLY SIGN-UP FEE OF <b>$30.00</b></h2>
<div class="abs outline banner-btn">GET STARTED</div>

<section class="abs lower"></section>
<h2 class="abs section-title benefits-title"><b>BENEFITS</b></h2>
<p class="abs benefits-text">Nam libero tempore, cum soluta nobis est eligendi optio cumque nihil impedit quo minus id quod maxime placeat.</p>
<ul class="abs benefit-list">
  <li><svg width="15" height="15" viewBox="0 0 16 16"><circle cx="8" cy="8" r="8" fill="#fff"/><path d="M4.5 8.3l2.3 2.3 4.7-4.9" fill="none" stroke="#4a5040" stroke-width="2"/></svg>Disability Compensation</li>
  <li><svg width="15" height="15" viewBox="0 0 16 16"><circle cx="8" cy="8" r="8" fill="#fff"/><path d="M4.5 8.3l2.3 2.3 4.7-4.9" fill="none" stroke="#4a5040" stroke-width="2"/></svg>Pension</li>
  <li><svg width="15" height="15" viewBox="0 0 16 16"><circle cx="8" cy="8" r="8" fill="#fff"/><path d="M4.5 8.3l2.3 2.3 4.7-4.9" fill="none" stroke="#4a5040" stroke-width="2"/></svg>Vocational Rehabilitation &amp; Employment</li>
  <li><svg width="15" height="15" viewBox="0 0 16 16"><circle cx="8" cy="8" r="8" fill="#fff"/><path d="M4.5 8.3l2.3 2.3 4.7-4.9" fill="none" stroke="#4a5040" stroke-width="2"/></svg>Dependents' Educational Assistance</li>
  <li><svg width="15" height="15" viewBox="0 0 16 16"><circle cx="8" cy="8" r="8" fill="#fff"/><path d="M4.5 8.3l2.3 2.3 4.7-4.9" fill="none" stroke="#4a5040" stroke-width="2"/></svg>Survivor Benefits</li>
  <li><svg width="15" height="15" viewBox="0 0 16 16"><circle cx="8" cy="8" r="8" fill="#fff"/><path d="M4.5 8.3l2.3 2.3 4.7-4.9" fill="none" stroke="#4a5040" stroke-width="2"/></svg>Life Insurance</li>
  <li><svg width="15" height="15" viewBox="0 0 16 16"><circle cx="8" cy="8" r="8" fill="#fff"/><path d="M4.5 8.3l2.3 2.3 4.7-4.9" fill="none" stroke="#4a5040" stroke-width="2"/></svg>Appeals Modernization</li>
</ul>
<div class="abs outline read-btn">READ MORE</div>

<h2 class="abs section-title news-title"><b>NEWS</b></h2>
<div class="news-item">
  <div class="abs news-photo" style="top:1614px;background:linear-gradient(90deg,#8a8f94,#b9b6ad 50%,#5c5a4e)" role="img" aria-label="Counsellor speaking with a veteran"></div>
  <h4 style="top:1607px">Finibus Bonorum et Malorum</h4>
  <div class="news-meta" style="top:1642px">
    <svg width="11" height="11" viewBox="0 0 11 11"><rect x="0.5" y="1.5" width="10" height="9" fill="none" stroke="#e4e6df"/><rect x="0.5" y="1.5" width="10" height="2.5" fill="#e4e6df"/></svg>13/02/2018 &nbsp;|&nbsp;
    <svg width="10" height="11" viewBox="0 0 10 11"><circle cx="5" cy="3" r="2.6" fill="#e4e6df"/><path d="M0 11c0-3.5 2.3-5 5-5s5 1.5 5 5z" fill="#e4e6df"/></svg>John Doe</div>
  <p style="top:1669px">Nam libero tempore, cum soluta nobis est eligendi optio cumque nihil impedit quo min..</p>
</div>
<div class="news-item">
  <div class="abs news-photo" style="top:1758px;background:linear-gradient(180deg,#7fa9d6,#b8c6cc 55%,#6f6446)" role="img" aria-label="Veteran in a wheelchair raising his arms outdoors"></div>
  <h4 style="top:1752px">Finibus Bonorum et Malorum</h4>
  <div class="news-meta" style="top:1787px">
    <svg width="11" height="11" viewBox="0 0 11 11"><rect x="0.5" y="1.5" width="10" height="9" fill="none" stroke="#e4e6df"/><rect x="0.5" y="1.5" width="10" height="2.5" fill="#e4e6df"/></svg>13/02/2018 &nbsp;|&nbsp;
    <svg width="10" height="11" viewBox="0 0 10 11"><circle cx="5" cy="3" r="2.6" fill="#e4e6df"/><path d="M0 11c0-3.5 2.3-5 5-5s5 1.5 5 5z" fill="#e4e6df"/></svg>John Doe</div>
  <p style="top:1814px">Nam libero tempore, cum soluta nobis est eligendi optio cumque nihil impedit quo min..</p>
</div>
<div class="abs outline view-btn">VIEW MORE</div>

<footer class="abs site-footer camo"></footer>
<div class="abs ficon" style="left:232px;top:2087px">
  <svg width="14" height="18" viewBox="0 0 14 18"><path d="M7 17C3 11 1 8.5 1 6a6 6 0 0 1 12 0c0 2.5-2 5-6 11z" fill="none" stroke="#fff" stroke-width="1.6"/><circle cx="7" cy="6" r="2" fill="#fff"/></svg></div>
<div class="abs ftext" style="left:293px;top:2087px">At vero eos et accus<br>amus et iusto odio dignissimos duci</div>
<div class="abs ficon" style="left:560px;top:2087px">
  <svg width="16" height="16" viewBox="0 0 16 16"><path d="M3 1l3 3-2 2c1 2 4 5 6 6l2-2 3 3-2 2C7 15 1 9 1 3z" fill="#fff"/></svg></div>
<div class="abs ftext" style="left:621px;top:2099px">1 888 888 8888</div>
<div class="abs ficon" style="left:766px;top:2087px">
  <svg width="18" height="14" viewBox="0 0 18 14"><rect x="0" y="0" width="18" height="14" rx="2" fill="#fff"/><path d="M1 1l8 6 8-6" fill="none" stroke="#2a3023" stroke-width="1.5"/></svg></div>
<div class="abs ftext" style="left:827px;top:2099px">info@harborwellnet.org</div>
<nav class="abs foot-nav">Home<span>|</span>About us<span>|</span>Services<span>|</span>Programs<span>|</span>Membership<span>|</span>News<span>|</span>Career<span>|</span>Contact us</nav>
<div class="abs rule"></div>
<div class="abs copyright">Copyrights © 2018, Harborwell Net. All rights reserved.</div>
<div class="abs social" style="left:979px"></div>
<div class="abs social" style="left:1022px"></div>
<div class="abs social" style="left:1065px"></div>
</body>
</html>
```